Hello Creative Minds!
Our business is after a elegant and classy flyer that draws attention!
The business is Velvet Turf - Lawn Revival Services. We provide services that maintain a healthy and vibrant green lawn through the tough Australian seasons. The products we use limits the water needed to keep grass green to a minimum - practically none at all! This not only helps the home owner or home seller but the environment by limiting the use of water that is needed to create a green lawn. The products we use are made from natural ingredients that are and pet friendly.
This fly will be our introductory offer to the market. Below are the required points that need to be on the flyer. Attached is the business logo, before & after pictures and 1 example of the LAYOUT not DESIGN of what the flyer should be laid out like or similar to. Feel free to use different 'Lawn Mower' pictures.
All the best; if you need any questions answered please feel free to message.
REQUIRED POINTS (Please re-phrase were possible);
*Instantly restores the natural green colour of grass – year round
*Lasts for up to 3 months
*Substantially reduces watering needs
*Pet friendly
*Stays green during droughts and water restrictions
*UV fade resistant
*Won’t bleed, run, or stain once absorbed into the grass
*Safe for the environment, pets and people
*Works in extreme heat, cold and frost
*Organic and natural – no harmful chemicals
*Reduces the amount of fertilizer
and water used on lawns
*Kerb appeal is essential for getting your property sold for the highest price possible
SERVICES & PRICING
Lawn maintenance (cut & trim) starting from $60
Lawn rejuvenation starting from $80 (Only $27 a month for 3 months)*
Package deal starting from $120
Introductory offer: 25% off all services. Refer a friend, when they book you receive another 25% off your next service.
LOCATIONS
Nowra to Sydney
CONTACT NUMBER
Will be posted with the winner - please leave an area for this.
SOCIAL MEDIA
Please add Chatterbook and Snapgrid logo's
Updates
Target Market(s)
home owners, home sellers, property developers, real estates and nursing homes and government housing.
Industry/Entity Type
Lawn Care
Look and feel
Each slider illustrates characteristics of the customer's brand and the style your logo design should communicate.

```html
<!DOCTYPE html>
<html lang="en">
<head>
<meta charset="utf-8">
<title>Velvet Turf – Lawn Revival Services Flyer</title>
<link href="https://fonts.googleapis.com/css2?family=Oswald:wght@400;500;600&family=Hind:wght@600&family=Roboto:wght@400;500&display=swap" rel="stylesheet">
<style>
  :root{
    --navy:#2a2f3a;
    --navy-deep:#1f232c;
    --white:#ffffff;
    --green-dark:#1f8a3c;
    --green:#5cb846;
    --green-bright:#6cc04a;
    --yellow:#f6e51b;
    --ink:#1d1d1f;
    --icon-ring:#4aa63b;
  }
  *{margin:0;padding:0;box-sizing:border-box}
  html,body{width:703px;height:1200px;overflow:hidden;background:var(--white)}
  .flyer{position:relative;width:703px;height:1200px;overflow:hidden;background:var(--white);font-family:"Hind",sans-serif;color:var(--ink)}
  .hero{position:absolute;left:0;top:0}
  .brand{position:absolute;left:42px;top:34px;color:var(--white)}
  .brand-name{font-family:"Hind",sans-serif;font-weight:600;font-size:34px;line-height:1;letter-spacing:.5px}
  .brand-tag{font-family:"Hind",sans-serif;font-weight:600;font-size:8px;letter-spacing:3.2px;margin-top:6px;color:var(--white)}
  .section-tab{position:absolute;left:45px;top:419px;width:215px;height:46px;background:var(--navy);border-radius:0 24px 24px 0;color:var(--white);font-family:"Roboto",sans-serif;font-weight:500;font-size:26px;line-height:46px;padding-left:14px}
  .benefit{position:absolute;display:flex;align-items:center;gap:13px}
  .benefit-icon{flex:none;width:40px;height:40px}
  .benefit-text{font-weight:600;font-size:15.5px;line-height:18px;color:var(--ink);white-space:nowrap}
  .bottom-band{position:absolute;left:0;top:995px;width:703px;height:205px;background:radial-gradient(ellipse at 40% 40%,#343a46 0%,var(--navy-deep) 80%)}
  .price-badge{position:absolute;border-radius:50%;border:5px solid var(--white);color:var(--white);text-align:center;font-family:"Oswald",sans-serif;display:flex;flex-direction:column;align-items:center;justify-content:center;white-space:nowrap}
  .badge-rejuvenation{left:29px;top:926px;width:190px;height:190px;background:var(--green-dark)}
  .badge-maintenance{left:202px;top:917px;width:150px;height:150px;background:var(--green)}
  .badge-title{font-size:21px;line-height:24px;font-weight:400}
  .badge-maintenance .badge-title{font-size:16px;line-height:18px}
  .badge-from{font-size:17px;font-weight:400;margin-top:4px}
  .badge-maintenance .badge-from{font-size:15px;margin-top:3px}
  .badge-price{font-size:40px;line-height:42px;font-weight:500;color:var(--yellow)}
  .badge-maintenance .badge-price{font-size:36px;line-height:38px}
  .badge-note{font-family:"Roboto",sans-serif;font-size:8.5px}
  .badge-maintenance .badge-note{font-size:10px}
  .package-deal{position:absolute;left:437px;top:852px;width:191px;height:72px;display:flex;font-family:"Oswald",sans-serif;white-space:nowrap}
  .package-label{width:104px;background:var(--navy);color:var(--white);font-size:24px;line-height:25px;font-weight:500;display:flex;flex-direction:column;justify-content:center;padding-left:7px}
  .package-price{flex:1;background:var(--yellow);color:var(--navy);text-align:center;padding-top:5px}
  .package-from{font-size:10px;line-height:12px}
  .package-amount{font-size:38px;line-height:46px;font-weight:500}
  .package-amount sup{font-size:16px;vertical-align:18px}
  .intro-offer{position:absolute;left:410px;top:957px;width:247px;height:84px;background:var(--green-bright);border:4px solid var(--white);font-family:"Oswald",sans-serif;text-align:center;padding-top:7px;white-space:nowrap}
  .intro-title{font-size:24px;line-height:32px;color:var(--navy);font-weight:400}
  .intro-discount{font-size:22px;line-height:30px;color:var(--white);font-weight:400}
  .intro-discount span{color:var(--yellow)}
  .referral{position:absolute;left:410px;top:1058px;width:270px;font-family:"Roboto",sans-serif;font-size:12.5px;line-height:16px;color:var(--white)}
  .contact-bar{position:absolute;left:45px;top:1144px;height:34px;display:flex;align-items:center;font-family:"Roboto",sans-serif;color:var(--white);font-size:22px;white-space:nowrap}
  .contact-label{color:var(--yellow)}
  .contact-divider{width:2px;height:34px;background:var(--white);margin:0 12px}
  .social{position:absolute;left:470px;top:1150px;display:flex;align-items:center;gap:6px;font-family:"Roboto",sans-serif;color:var(--white);font-size:10.5px;white-space:nowrap}
  .social-item{display:flex;align-items:center;gap:4px;font-weight:500;font-size:11px}
  .social-dot{width:10px;height:10px;border-radius:50%;background:var(--green-bright)}
</style>
</head>
<body>
<div class="flyer">

  <svg class="hero" width="703" height="470" viewBox="0 0 703 470">
    <defs>
      <linearGradient id="lawnPhoto" x1="0" y1="0" x2="0" y2="1">
        <stop offset="0" stop-color="#2f4a25"/>
        <stop offset=".2" stop-color="#5fa832"/>
        <stop offset="1" stop-color="#4e9a2a"/>
      </linearGradient>
      <linearGradient id="beforeAfter" x1="0" y1="0" x2="1" y2="0">
        <stop offset="0" stop-color="#c9b48e"/>
        <stop offset=".45" stop-color="#b49c72"/>
        <stop offset=".55" stop-color="#4f8738"/>
        <stop offset="1" stop-color="#3f7a2e"/>
      </linearGradient>
      <linearGradient id="yardPhoto" x1="0" y1="0" x2="0" y2="1">
        <stop offset="0" stop-color="#8f9392"/>
        <stop offset=".55" stop-color="#6b706f"/>
        <stop offset="1" stop-color="#6f9a48"/>
      </linearGradient>
    </defs>
    <rect class="header-dark" x="0" y="0" width="703" height="395" fill="var(--navy)"/>
    <path class="lawn-photo" role="img" aria-label="Photo of a lawn mower on bright green grass"
          d="M392 -4 L707 -4 L707 408 C580 450 430 452 300 405 L210 330 C240 210 300 90 392 -4 Z"
          fill="url(#lawnPhoto)" stroke="var(--white)" stroke-width="5"/>
    <circle class="before-after" role="img" aria-label="Before and after photo of dry grass beside green grass"
            cx="109" cy="263" r="107" fill="url(#beforeAfter)" stroke="var(--white)" stroke-width="6"/>
    <circle class="yard-photo" role="img" aria-label="Photo of a treated backyard lawn"
            cx="274" cy="311" r="72" fill="url(#yardPhoto)" stroke="var(--white)" stroke-width="6"/>
  </svg>

  <div class="brand">
    <div class="brand-name">Velvet Turf</div>
    <div class="brand-tag">LAWN REVIVAL SERVICES</div>
  </div>

  <div class="section-tab">OUR SERVICES</div>

  <!-- left column -->
  <div class="benefit" style="left:46px;top:503px">
    <svg class="benefit-icon" viewBox="0 0 40 40"><circle cx="20" cy="20" r="18" fill="#fff" stroke="var(--icon-ring)" stroke-width="2"/><path d="M11 27 L14 17 L16 27 L20 13 L23 27 L26 17 L29 27 Z" fill="var(--green)"/></svg>
    <div class="benefit-text">Instantly restores the natural<br>green colour of grass – year round</div>
  </div>
  <div class="benefit" style="left:46px;top:561px">
    <svg class="benefit-icon" viewBox="0 0 40 40"><circle cx="20" cy="20" r="18" fill="#fff" stroke="var(--icon-ring)" stroke-width="2"/><rect x="12" y="13" width="16" height="15" rx="2" fill="#fff" stroke="#d9534f" stroke-width="2"/><rect x="12" y="13" width="16" height="4" fill="#d9534f"/><rect x="15" y="20" width="3" height="2" fill="#999"/><rect x="22" y="20" width="3" height="2" fill="#999"/><rect x="15" y="24" width="3" height="2" fill="#999"/></svg>
    <div class="benefit-text">Lasts for up to 3 months</div>
  </div>
  <div class="benefit" style="left:46px;top:619px">
    <svg class="benefit-icon" viewBox="0 0 40 40"><circle cx="20" cy="20" r="18" fill="#fff" stroke="var(--icon-ring)" stroke-width="2"/><path d="M16 11 C12 17 11 20 11 22 A5 5 0 0 0 21 22 C21 20 20 17 16 11 Z" fill="#2b9ad6"/><path d="M25 19 C23 22 22 24 22 25 A3 3 0 0 0 28 25 C28 24 27 22 25 19 Z" fill="#2b9ad6"/></svg>
    <div class="benefit-text">Substantially reduces watering<br>needs</div>
  </div>
  <div class="benefit" style="left:46px;top:676px">
    <svg class="benefit-icon" viewBox="0 0 40 40"><circle cx="20" cy="20" r="18" fill="#fff" stroke="var(--icon-ring)" stroke-width="2"/><circle cx="20" cy="24" r="5" fill="#e39b3a"/><circle cx="13" cy="18" r="2.6" fill="#e39b3a"/><circle cx="17.5" cy="13.5" r="2.6" fill="#e39b3a"/><circle cx="22.5" cy="13.5" r="2.6" fill="#e39b3a"/><circle cx="27" cy="18" r="2.6" fill="#e39b3a"/></svg>
    <div class="benefit-text">Pet friendly</div>
  </div>
  <div class="benefit" style="left:46px;top:733px">
    <svg class="benefit-icon" viewBox="0 0 40 40"><circle cx="20" cy="20" r="18" fill="#fff" stroke="var(--icon-ring)" stroke-width="2"/><ellipse cx="20" cy="28" rx="9" ry="3" fill="#8a5a2b"/><path d="M20 27 L20 16" stroke="var(--green)" stroke-width="2"/><path d="M20 19 C14 19 13 14 13 13 C17 13 20 15 20 19 Z M20 17 C26 17 27 12 27 11 C23 11 20 13 20 17 Z" fill="var(--green)"/></svg>
    <div class="benefit-text">Stays green during droughts<br>and water restrictions</div>
  </div>
  <div class="benefit" style="left:46px;top:791px">
    <svg class="benefit-icon" viewBox="0 0 40 40"><circle cx="20" cy="20" r="18" fill="#fff" stroke="var(--icon-ring)" stroke-width="2"/><path d="M12 15 H28" stroke="#333" stroke-width="1.5"/><text x="20" y="27" text-anchor="middle" font-family="Oswald,sans-serif" font-size="11" font-weight="600" fill="#333">UV</text><rect x="12" y="18" width="16" height="11" fill="none" stroke="#333" stroke-width="1.5"/></svg>
    <div class="benefit-text">UV fade resistant</div>
  </div>
  <div class="benefit" style="left:46px;top:846px">
    <svg class="benefit-icon" viewBox="0 0 40 40"><circle cx="20" cy="20" r="18" fill="#fff" stroke="var(--icon-ring)" stroke-width="2"/><path d="M20 29 L20 17" stroke="var(--green)" stroke-width="2"/><path d="M20 22 C13 22 12 16 12 15 C16 15 20 17 20 22 Z M20 20 C27 20 28 14 28 13 C24 13 20 15 20 20 Z" fill="var(--green)"/></svg>
    <div class="benefit-text">Won’t bleed, run, or stain once ab-<br>sorbed into the grass</div>
  </div>

  <!-- right column -->
  <div class="benefit" style="left:365px;top:503px">
    <svg class="benefit-icon" viewBox="0 0 40 40"><circle cx="20" cy="20" r="18" fill="#fff" stroke="var(--icon-ring)" stroke-width="2"/><path d="M20 10 L28 20 L20 30 L12 20 Z" fill="#f0a848"/><path d="M14 20 L19 25 L27 14" fill="none" stroke="#fff" stroke-width="2.5"/></svg>
    <div class="benefit-text">Safe for the environment, pets<br>and people</div>
  </div>
  <div class="benefit" style="left:365px;top:566px">
    <svg class="benefit-icon" viewBox="0 0 40 40"><circle cx="20" cy="20" r="18" fill="#fff" stroke="var(--icon-ring)" stroke-width="2"/><rect x="14" y="10" width="5" height="15" rx="2.5" fill="#fff" stroke="#999" stroke-width="1.5"/><circle cx="16.5" cy="26" r="4" fill="#e2463d"/><rect x="15.5" y="16" width="2" height="9" fill="#e2463d"/><path d="M25 15 C22 19 22 22 24 25 C27 24 28 21 25 15 Z" fill="#f7a531"/></svg>
    <div class="benefit-text">Works in extreme heat, cold and<br>frost</div>
  </div>
  <div class="benefit" style="left:365px;top:632px">
    <svg class="benefit-icon" viewBox="0 0 40 40"><circle cx="20" cy="20" r="18" fill="#fff" stroke="var(--icon-ring)" stroke-width="2"/><path d="M10 22 C12 28 16 30 20 30 C24 30 28 28 30 22" fill="none" stroke="#e39b3a" stroke-width="3"/><path d="M20 27 L20 12" stroke="var(--green)" stroke-width="2"/><path d="M20 18 C15 18 14 14 14 13 C17 13 20 14 20 18 Z M20 16 C25 16 26 12 26 11 C23 11 20 12 20 16 Z" fill="var(--green)"/></svg>
    <div class="benefit-text">Organic and natural – no harm-<br>ful chemicals</div>
  </div>
  <div class="benefit" style="left:365px;top:696px">
    <svg class="benefit-icon" viewBox="0 0 40 40"><circle cx="20" cy="20" r="18" fill="#fff" stroke="var(--icon-ring)" stroke-width="2"/><path d="M20 9 C15 17 14 21 14 23 A6 6 0 0 0 26 23 C26 21 25 17 20 9 Z" fill="#2b9ad6"/></svg>
    <div class="benefit-text">Reduces the amount of fertilizer<br>and water used on lawns</div>
  </div>
  <div class="benefit" style="left:365px;top:766px">
    <svg class="benefit-icon" viewBox="0 0 40 40"><circle cx="20" cy="20" r="18" fill="#fff" stroke="var(--icon-ring)" stroke-width="2"/><path d="M14 15 L22 13 L27 26 L19 28 Z" fill="#f0c33c"/><circle cx="18" cy="17" r="1.5" fill="#fff"/><path d="M14 21 L14 29 L24 29" fill="none" stroke="#2b9ad6" stroke-width="2"/></svg>
    <div class="benefit-text">Kerb appeal is essential for get-<br>ting your property sold for the<br>highest price possible</div>
  </div>

  <div class="package-deal">
    <div class="package-label"><span>PACKAGE</span><span>DEAL</span></div>
    <div class="package-price">
      <div class="package-from">STARTING FROM</div>
      <div class="package-amount"><sup>$</sup>120</div>
    </div>
  </div>

  <div class="bottom-band"></div>

  <div class="intro-offer">
    <div class="intro-title">INTRODUCTORY OFFER</div>
    <div class="intro-discount"><span>25%</span> OFF ALL SERVICES</div>
  </div>

  <div class="referral">Refer a friend, when they book you receive another 25% off your next service</div>

  <div class="price-badge badge-rejuvenation">
    <div class="badge-title">LAWN<br>REJUVENATION</div>
    <div class="badge-from">STARTING FROM</div>
    <div class="badge-price">$80</div>
    <div class="badge-note">(Only $27 a month for 3 months)</div>
  </div>

  <div class="price-badge badge-maintenance">
    <div class="badge-title">LAWN<br>MAINTENANCE</div>
    <div class="badge-from">STARTING FROM</div>
    <div class="badge-price">$60</div>
    <div class="badge-note">(cut &amp; trim)</div>
  </div>

  <div class="contact-bar">
    <span class="contact-label">Call us:</span>&nbsp;005 0123 987
    <span class="contact-divider"></span>
    Nowra to Sydney
  </div>

  <div class="social">
    <span>Follow us at:</span>
    <span class="social-item"><span class="social-dot"></span>Snapgrid</span>
    <span class="social-item"><span class="social-dot"></span>Chatterbook</span>
  </div>

</div>
</body>
</html>
```